Business Card & Letterhead Design

We a financial advice company based in Australia. We provide advice to wealthy farmers.

We are changing our business name FROM Brightvale Financial TO Tallowmere Wealth and we need a new letterhead and double sided business card design

Attached is designs from our previous branding (Brightvale Financial) as it includes all the details we require on the new Tallowmere Wealth business cards and letterhead.

Need extra days to review

```html
<!DOCTYPE html>
<html lang="en">
<head>
<meta charset="utf-8">
<title>Tallowmere Wealth – Business Card</title>
<link href="https://fonts.googleapis.com/css2?family=Cinzel:wght@400;500&family=Montserrat:wght@400;500&display=swap" rel="stylesheet">
<style>
  :root{
    --backdrop:#2b2b2b;
    --slate:#5b676e;
    --charcoal:#4a4a4b;
    --paper:#ffffff;
    --ink:#4a4a4b;
    --rule:#8f9498;
    --soft:#e9ecee;
    --accent:#7f97ad;
  }
  *{box-sizing:border-box;margin:0;padding:0}
  html,body{width:1200px;height:900px;overflow:hidden;background:var(--backdrop)}
  .canvas{position:relative;width:1200px;height:900px}
  .card{position:absolute;width:620px;height:354px;border-radius:22px;overflow:hidden;
        box-shadow:0 14px 30px rgba(0,0,0,.45)}
  .serif{font-family:"Cinzel",serif}
  .sans{font-family:"Montserrat",sans-serif}

  /* front */
  .card-front{left:80px;top:90px;background:var(--slate);color:var(--paper)}
  .front-brand{position:absolute;left:48px;top:70px;font-size:26px;letter-spacing:1px;font-weight:400}
  .services{position:absolute;left:50px;top:128px;list-style:none}
  .services li{display:flex;align-items:center;gap:12px;font-size:18px;letter-spacing:.5px;margin-bottom:9px}
  .services .dot{width:16px;height:16px;border:1.5px solid var(--paper);border-radius:50%}
  .licensee{position:absolute;left:50px;top:272px;font-size:13.5px;line-height:1.6;letter-spacing:.2px}
  .front-circle{position:absolute;right:54px;top:36px;width:168px;height:168px;border:4px solid var(--paper);border-radius:50%}

  /* back */
  .card-back{left:500px;top:470px;background:var(--paper);color:var(--ink)}
  .back-top{position:absolute;left:0;top:0;width:100%;height:212px;background:var(--paper)}
  .back-rule{position:absolute;left:0;top:118px;width:100%;height:6px;background:var(--soft);border-top:1px solid var(--rule)}
  .motto{position:absolute;right:34px;top:24px;font-size:14px;letter-spacing:.5px}
  .person{position:absolute;right:34px;top:46px;text-align:right;font-size:12.5px;line-height:1.45}
  .person .name{font-family:"Cinzel",serif;font-size:19px;letter-spacing:.5px;color:#6a6d70}
  .brand-lockup{position:absolute;left:34px;top:142px;display:flex;align-items:center;gap:12px}
  .brand-lockup .mark{width:44px;height:44px;border:2.5px solid var(--ink);border-radius:50%}
  .brand-lockup .word{font-family:"Cinzel",serif;font-size:24px;color:var(--ink);letter-spacing:.5px}
  .back-band{position:absolute;left:0;top:212px;width:100%;height:142px;background:var(--charcoal);color:var(--paper)}
  .contacts{position:absolute;left:30px;top:18px;list-style:none;font-size:13.5px}
  .contacts li{display:flex;align-items:center;gap:11px;margin-bottom:6px}
  .contacts svg{width:14px;height:14px;fill:var(--paper)}
  .address{position:absolute;right:34px;top:18px;text-align:right;font-size:13.5px;line-height:1.45}
  .address .tag{margin-top:10px;font-size:15px}
  .edge-tab{position:absolute;right:0;top:24px;width:22px;height:6px;background:var(--accent)}
</style>
</head>
<body>
<div class="canvas">

  <section class="card card-front">
    <div class="front-brand serif">TALLOWMERE WEALTH</div>
    <ul class="services serif">
      <li><span class="dot"></span>LIFE &amp; TPD INSURANCE</li>
      <li><span class="dot"></span>INCOME PROTECTION</li>
      <li><span class="dot"></span>FINANCIAL PLANNING</li>
      <li><span class="dot"></span>RETIREMENT PLANNING</li>
    </ul>
    <p class="licensee sans">Kestrel Advice Group Limited<br>Australian Financial Services Licensee-License Number 418203</p>
    <div class="front-circle"></div>
  </section>

  <section class="card card-back">
    <div class="back-top">
      <p class="motto serif">'FINANCIAL PEACE OF MIND'</p>
      <div class="person sans">
        <span class="name">SAM HOLLIS</span> | B.Ag.Ec. Dip F.P. CFP®<br>
        Managing Director<br>
        Authorised Representative
      </div>
      <div class="back-rule"></div>
      <div class="brand-lockup">
        <span class="mark"></span>
        <span class="word">TALLOWMERE WEALTH</span>
      </div>
    </div>
    <div class="back-band sans">
      <ul class="contacts">
        <li><svg viewBox="0 0 16 16"><rect x="4" y="1" width="8" height="14" rx="1.5"/></svg>0400 555 218</li>
        <li><svg viewBox="0 0 16 16"><path d="M2 6c0-3 12-3 12 0v2h-3V6H5v2H2zM3 9h10l1 5H2z"/></svg>(07) 3555 0142</li>
        <li><svg viewBox="0 0 16 16"><path d="M4 2h8v4H4zM2 7h12v6h-2v2H4v-2H2z"/></svg>(07) 3555 0198</li>
        <li><svg viewBox="0 0 16 16"><path d="M1 3h14v10H1zM2 4l6 5 6-5" fill="none" stroke="#fff" stroke-width="1.5"/></svg>sam@tallowmerewealth.com.au</li>
        <li><svg viewBox="0 0 16 16"><circle cx="8" cy="8" r="6.5" fill="none" stroke="#fff" stroke-width="1.5"/><path d="M1.5 8h13M8 1.5c-3 3.5-3 9.5 0 13M8 1.5c3 3.5 3 9.5 0 13" fill="none" stroke="#fff" stroke-width="1"/></svg>www.tallowmerewealth.com.au</li>
      </ul>
      <div class="address">
        Suite 4C, 18 Merrow St<br>
        Riverbend QLD 4170<br>
        PO Box 5512<br>
        Eastvale QLD 4170
        <p class="tag">A referral built business</p>
      </div>
      <div class="edge-tab"></div>
    </div>
  </section>

</div>
</body>
</html>
```